New bussiness card, using company logo.
Lionel Brisk
Manager/Director
Brisk Property Developments
Po Box 5347
Harbourview Central
Vic
0491 638 205
lionel@briskpropertydevelopments
eye catching, vibrant colours, professional

```html
<!DOCTYPE html>
<html lang="en">
<head>
<meta charset="utf-8">
<title>Brisk Property Developments – Business Cards</title>
<link href="https://fonts.googleapis.com/css2?family=Open+Sans:wght@400;600;700&display=swap" rel="stylesheet">
<style>
  :root {
    --backdrop: #2b2623;
    --card-white: #ffffff;
    --brand-red: #de2a2f;
    --brand-green: #6cbd45;
    --brand-green-light: #8cc63f;
    --ink: #222222;
    --ink-soft: #555555;
  }
  * { box-sizing: border-box; margin: 0; padding: 0; }
  html, body {
    width: 1200px; height: 736px; overflow: hidden;
    background: var(--backdrop);
    font-family: "Open Sans", Arial, sans-serif;
  }
  .sheet { position: relative; width: 1200px; height: 736px; }
  .card {
    position: absolute; width: 556px; height: 316px;
    border-radius: 22px; overflow: hidden;
  }
  .card--front { left: 27px; top: 36px; background: var(--card-white); }
  .card--red { left: 609px; top: 36px; background: var(--brand-red); }
  .card--white { left: 27px; top: 386px; background: var(--card-white); }
  .card--green { left: 612px; top: 384px; background: linear-gradient(90deg, var(--brand-green-light), var(--brand-green)); }

  .brand-name {
    position: absolute; left: 0; right: 0; text-align: center;
    font-weight: 700; line-height: 1.2; white-space: nowrap;
  }
  .card--front .brand-name { top: 82px; font-size: 20px; color: var(--brand-red); }
  .card--red .brand-name { top: 140px; font-size: 27px; color: var(--card-white); }
  .card--white .brand-name { top: 108px; font-size: 26px; color: var(--brand-red); }
  .card--green .brand-name { top: 138px; font-size: 29px; color: var(--card-white); }

  .swoosh { position: absolute; left: 0; top: 0; width: 556px; height: 316px; }

  .holder {
    position: absolute; top: 187px; left: 0; right: 0; text-align: center;
    color: var(--ink-soft); font-size: 15px;
  }
  .holder__name { color: var(--brand-red); font-weight: 700; font-size: 19px; }

  .contact {
    position: absolute; left: 0; right: 0; text-align: center;
    color: var(--card-white); font-size: 13px;
  }
  .contact--address { top: 259px; }
  .contact--lines { top: 283px; display: flex; justify-content: center; gap: 16px; }
  .contact__item { display: inline-flex; align-items: center; gap: 6px; }
  .contact__item svg { width: 11px; height: 11px; fill: var(--card-white); }

  .website {
    position: absolute; left: 0; right: 0; text-align: center;
    font-size: 15px; letter-spacing: 1px;
  }
  .card--red .website { top: 274px; color: var(--card-white); }
  .card--white .website { top: 272px; color: var(--ink); }
  .card--green .website { top: 275px; color: var(--card-white); }
</style>
</head>
<body>
<main class="sheet">

  <section class="card card--front">
    <svg class="swoosh" viewBox="0 0 556 316" aria-hidden="true">
      <path d="M0 190 Q278 262 556 190 L556 316 L0 316 Z" fill="var(--brand-green)"/>
      <path d="M0 190 Q278 262 556 190 L556 202 Q278 250 0 208 Z" fill="var(--brand-red)"/>
    </svg>
    <p class="brand-name">Brisk Property Developments</p>
    <p class="holder"><span class="holder__name">Lionel Brisk,</span> Manager/Director</p>
    <p class="contact contact--address">Po Box 5347, Harbourview Central , Vic</p>
    <p class="contact contact--lines">
      <span class="contact__item">
        <svg viewBox="0 0 24 24" aria-hidden="true"><path d="M6.6 10.8a15.1 15.1 0 0 0 6.6 6.6l2.2-2.2c.3-.3.7-.4 1-.2 1.1.4 2.3.6 3.6.6.6 0 1 .4 1 1V20c0 .6-.4 1-1 1A17 17 0 0 1 3 4c0-.6.4-1 1-1h3.5c.6 0 1 .4 1 1 0 1.3.2 2.5.6 3.6.1.3 0 .7-.2 1z"/></svg>
        0491 638 205
      </span>
      <span class="contact__item">
        <svg viewBox="0 0 24 24" aria-hidden="true"><path d="M2 5h20v14H2z M2 5l10 8 10-8" fill="none" stroke="#fff" stroke-width="2.5"/></svg>
        lionel@briskpropertydevelopments.com
      </span>
    </p>
  </section>

  <section class="card card--red">
    <p class="brand-name">Brisk Property Developments</p>
    <p class="website">www.briskpropertydevelopments.com</p>
  </section>

  <section class="card card--white">
    <p class="brand-name">Brisk Property Developments</p>
    <p class="website">www.briskpropertydevelopments.com</p>
  </section>

  <section class="card card--green">
    <p class="brand-name">Brisk Property Developments</p>
    <p class="website">www.briskpropertydevelopments.com</p>
  </section>

</main>
</body>
</html>
```